Honey Company from Florida Needs Sweet and Buzz-worthy Site

Website Requests:
-Deluxe 5-Page Website with SSL-Secure Online Store (Shopify)
-High-end imagery to appeal to a discerning consumer
-Detailed verbiage with strong SEO and easy readability
-Design principles: simple, chic, luxe, earthy
Pages:
1. Home {Local, Raw American Honey from Florida}
2. The Hive
> About Us
>Meet the Beekeepers
3. Buy Honey
> Shopify retail store
4. The Buzz {News, Recipes & More}
> Blog
5. Contact Us {We're Buzzin' to Meet You}
> Store Hours
> Phone Number
> Address
> Quick Contact Form
Attachments: Web design notes, Logo, Color Codes, Inspiration Photos
Target Market(s)
High-end honey consumer in the U.S.
Industry/Entity Type
Upscale honey enthusiasts; direct to consumer sales.
Coding
Coded - Design and coding required
Number of Pages Required
5+ page
Requirements
Must have
- Upscale look and feel, easy usability for quick sales.

```html
<!DOCTYPE html>
<html lang="en">
<head>
<meta charset="utf-8">
<title>Golden Comb Company – Local Raw Honey</title>
<link rel="stylesheet" href="https://fonts.googleapis.com/css2?family=Arvo:wght@700&family=Lato:ital,wght@0,400;0,700;1,400&display=swap">
<style>
:root{
  --gold:#b8892b;
  --gold-light:#d9a53a;
  --ink:#1b1b1b;
  --dark:#141414;
  --black:#0b0b0b;
  --white:#ffffff;
  --text:#2a2a2a;
  --muted:#cfcfcf;
}
*{box-sizing:border-box;margin:0;padding:0}
html,body{width:1200px;height:3476px;overflow:hidden}
body{font-family:"Lato",sans-serif;color:var(--text);background:var(--white);position:relative}
.slab{font-family:"Arvo",serif;font-weight:700}
a{color:inherit;text-decoration:none}

.promo-bar{height:59px;background:var(--dark);color:var(--gold-light);font-size:14px;font-weight:700;display:flex;align-items:center;justify-content:center}

.site-header{height:110px;background:var(--white);position:relative}
.header-logo{position:absolute;left:76px;top:-5px;width:174px;height:174px;border-radius:50%;background:var(--white);border:3px solid var(--ink);box-shadow:0 0 0 6px var(--white);display:flex;align-items:center;justify-content:center;text-align:center;z-index:3}
.brand-name{font-family:"Lato",sans-serif;font-weight:700;color:var(--ink);text-transform:uppercase;line-height:1.15}
.header-logo .brand-name{font-size:22px}
.main-nav{position:absolute;right:72px;top:0;height:110px;display:flex;align-items:center;gap:44px;font-size:13px;font-weight:700;color:var(--ink)}
.main-nav .active{color:var(--gold)}
.nav-icons{display:flex;gap:30px;align-items:center}
.cart{position:relative}
.cart-count{position:absolute;top:-12px;right:-14px;width:18px;height:18px;border-radius:50%;background:var(--gold);color:var(--white);font-size:10px;display:flex;align-items:center;justify-content:center}

.hero{height:657px;position:relative;background:linear-gradient(100deg,#3b3a1c 0%,#6a5a2a 30%,#b06a1a 60%,#e08a1a 75%,#7a4a18 100%)}
.hero-photo{position:absolute;inset:0}
.hero-copy{position:absolute;left:74px;top:165px;color:var(--white)}
.hero-copy h1{font-size:80px;line-height:76px}
.hero-copy p{font-size:27px;line-height:38px;margin-top:12px}
.btn{display:inline-block;background:var(--gold);color:var(--white);font-family:"Arvo",serif;font-weight:700}
.hero .btn{margin-top:30px;font-size:24px;padding:12px 32px}
.hero-badge{position:absolute;left:810px;top:330px;width:260px;height:260px;border-radius:50%;background:var(--white);border:4px solid var(--ink);box-shadow:0 0 0 8px var(--white);display:flex;align-items:center;justify-content:center;text-align:center}
.hero-badge .brand-name{font-size:32px}

.intro{height:745px;position:relative}
.intro-copy{position:absolute;left:74px;top:62px;width:506px}
.intro-copy h2{font-size:42px;line-height:52px;color:var(--ink)}
.intro-copy p{font-size:16px;line-height:27.5px;margin-top:12px}
.intro-copy h2+p{margin-top:30px}
.btn-small{font-size:17px;padding:11px 26px;margin-top:34px}
.intro-photo{position:absolute;left:616px;top:69px;width:511px;height:595px;background:linear-gradient(160deg,#efece6,#d9b98a 55%,#c99542)}

.bees-band{height:605px;position:relative;background:linear-gradient(90deg,#c87a18 0%,#e6a23a 25%,#6b6a2a 55%,#7e9a45 75%,#b6c073 100%)}
.quote-box{position:absolute;left:255px;top:77px;width:691px;height:451px;background:rgba(20,20,20,.9);text-align:center;color:var(--white);padding-top:40px}
.eyebrow{color:var(--gold-light);font-size:31px}
.quote-box h2{font-size:41px;line-height:50px;margin-top:6px}
.quote-box blockquote{font-style:italic;font-size:24px;line-height:39px;margin:32px auto 0;width:610px}

.benefits{height:767px;position:relative}
.benefits-photo{position:absolute;left:77px;top:81px;width:511px;height:595px;background:linear-gradient(170deg,#e9c9a5,#c4824a 50%,#a74a2a)}
.benefits-copy{position:absolute;left:624px;top:156px;width:506px}
.benefits-copy .eyebrow{color:var(--gold);font-size:31px}
.benefits-copy h2{font-size:42px;line-height:51px;color:var(--ink);margin-top:8px}
.benefits-copy p{font-size:16px;line-height:29.5px;margin-top:24px}

.signup{height:162px;background:var(--black);position:relative;color:var(--white)}
.signup h2{position:absolute;left:74px;top:50px;font-size:35px}
.signup-form{position:absolute;left:616px;top:50px;display:flex;height:56px}
.signup-form .field{width:389px;background:var(--white);color:#444;font-size:15px;display:flex;align-items:center;padding-left:14px}
.signup-form .btn{width:122px;display:flex;align-items:center;justify-content:center;font-size:18px}

.site-footer{height:283px;background:var(--black);border-top:1px solid #222;position:relative;color:var(--white)}
.footer-logo{position:absolute;left:75px;top:42px;width:115px;height:115px;border-radius:50%;background:var(--white);border:2px solid var(--ink);box-shadow:0 0 0 4px var(--white);display:flex;align-items:center;justify-content:center;text-align:center}
.footer-logo .brand-name{font-size:14px}
.follow{position:absolute;left:74px;top:178px;font-size:20px}
.social{display:flex;gap:22px;margin-top:14px}
.social span{width:30px;height:30px;border-radius:50%;background:var(--white)}
.footer-col{position:absolute;top:62px;font-size:15px}
.footer-col h3{font-family:"Arvo",serif;font-size:18px;margin-bottom:16px}
.footer-col li{list-style:none;line-height:32px}

.legal{height:88px;background:#1b1b1b;color:var(--white);position:relative;font-size:13px}
.legal p{position:absolute;left:76px;top:38px}
.cards{position:absolute;left:842px;top:30px;display:flex;gap:9px}
.cards span{width:40px;height:26px;background:var(--white);border-radius:3px}
.legal .count{position:absolute;right:16px;top:40px;font-size:12px}
</style>
</head>
<body>

<div class="promo-bar">Save 40% with our December Sale</div>

<header class="site-header">
  <div class="header-logo"><span class="brand-name">Golden<br>Comb<br>Company</span></div>
  <nav class="main-nav">
    <a class="active" href="#">HOME</a>
    <a href="#">THE HIVE</a>
    <a href="#">BUY HONEY</a>
    <a href="#">THE BUZZ</a>
    <a href="#">CONTACT US</a>
    <span class="nav-icons">
      <svg width="16" height="16" viewBox="0 0 16 16"><circle cx="6.5" cy="6.5" r="4.5" fill="none" stroke="#1b1b1b" stroke-width="2"/><line x1="10" y1="10" x2="14" y2="14" stroke="#1b1b1b" stroke-width="2.4"/></svg>
      <svg width="16" height="16" viewBox="0 0 16 16"><circle cx="8" cy="5" r="3.5" fill="#1b1b1b"/><path d="M1 16c0-5 3-7 7-7s7 2 7 7z" fill="#1b1b1b"/></svg>
      <span class="cart"><svg width="18" height="16" viewBox="0 0 18 16"><path d="M1 5h16l-2 10H3z" fill="#1b1b1b"/><path d="M5 5l4-4 4 4" fill="none" stroke="#1b1b1b" stroke-width="1.6"/></svg><span class="cart-count">0</span></span>
    </span>
  </nav>
</header>

<section class="hero">
  <div class="hero-photo" role="img" aria-label="Photo of a honey jar with a dipper dripping honey beside wildflowers"></div>
  <div class="hero-copy">
    <h1 class="slab">Blessed to<br>Bee-Keep</h1>
    <p>Straight from our beloved hives to<br>your lovely home.</p>
    <a class="btn" href="#">Shop Now</a>
  </div>
  <div class="hero-badge"><span class="brand-name">Golden<br>Comb<br>Company</span></div>
</section>

<section class="intro">
  <div class="intro-copy">
    <h2 class="slab">Local, Raw American<br>Honey from Florida</h2>
    <p>100% raw, unfiltered Florida honey straight from he beehives on his six-acre property, Golden Comb Honey Farm, 1418<br>County Road 12 in Lakeview.</p>
    <p>Agricultural Company specializing in the Production of 100% Raw American Honey, and the Pollination of America's food<br>crops.</p>
    <p>Our Honey comes straight from our beehives to your table. No filtering, heating, or any funny stuff. Just All Natural, 100% Pure Florida Honey Natural Wild Honey- flavors include Orange Blossom, Gallberry, Summer Wildflower, Winter Wildflower, and many more. Bee Pollen, Royal Jelly, and Bee venom. Bee removals are done by Daniel Marlow, owner of Golden Comb Honey Farm, has about 1,200 beehives that he moves around to pollinate different plants.</p>
    <a class="btn btn-small" href="#">READ MORE</a>
  </div>
  <div class="intro-photo" role="img" aria-label="Photo of a small honey jar and wooden dipper in a kraft gift box with paper shred"></div>
</section>

<section class="bees-band" role="img" aria-label="Photo of honeybees on golden honeycomb">
  <div class="quote-box">
    <p class="eyebrow slab">Importance of Bees</p>
    <h2 class="slab">Don't Judge a Bee by<br>Its Stinger</h2>
    <blockquote>“Over one-third of our entire diet is dependent on pollination from the honeybee. So, for every three bites of food you eat, you can thank the honeybee for one of those three bites,”</blockquote>
  </div>
</section>

<section class="benefits">
  <div class="benefits-photo" role="img" aria-label="Photo of a woman drizzling honey while baking in a kitchen"></div>
  <div class="benefits-copy">
    <p class="eyebrow slab">The health benefits of honey</p>
    <h2 class="slab">Real Local Honey,<br>Really Good for You</h2>
    <p>Raw honey is loaded with antioxidants to protect your body from cell damage due to free radicals. Honey has been long known as a folk remedy to help heal burns and wounds due to its antibacterial and antifungal properties. Honey is also very well known to soothe a sore throat. Try taking a spoonful of honey and add it to hot tea if you feel like you have a cold.<br>Honey can also help as a cough suppressant.</p>
    <a class="btn btn-small" href="#">READ MORE</a>
  </div>
</section>

<section class="signup">
  <h2 class="slab">Sign-up for Our Emails</h2>
  <div class="signup-form">
    <div class="field">Enter Email Address</div>
    <a class="btn" href="#">Subscribe</a>
  </div>
</section>

<footer class="site-footer">
  <div class="footer-logo"><span class="brand-name">Golden<br>Comb<br>Company</span></div>
  <div class="follow">Follow Us
    <div class="social"><span></span><span></span><span></span><span></span><span></span></div>
  </div>
  <div class="footer-col" style="left:421px"><h3>COMPANY</h3><ul><li>Nemo enim ipsam</li><li>Voluptatem</li><li>Quia voluptas sit</li><li>Aspernatur</li></ul></div>
  <div class="footer-col" style="left:665px"><h3>SUPPORT</h3><ul><li>Nemo enim ipsam</li><li>Voluptatem</li><li>Quia voluptas sit</li><li>Aspernatur</li></ul></div>
  <div class="footer-col" style="left:909px"><h3>STORES</h3><ul><li>Nemo enim ipsam</li><li>Voluptatem</li><li>Quia voluptas sit</li><li>Aspernatur</li></ul></div>
</footer>

<div class="legal">
  <p>Copyright © 2021 CompanyName All Rights Reserved.</p>
  <div class="cards"><span></span><span></span><span></span><span></span><span></span><span></span></div>
  <span class="count">x10</span>
</div>

</body>
</html>
```